Design a website for our small self storage business

We're looking for a freelance web designer who can produce a good-looking design for our small business website (no coding necessary). We will provide a list of pages to design, along with content outlines.

Key skills:
- Graphic design
- Responsive web design
- Proficiency with a modern web design tool such as Figma, Adobe Xd, or InVision

Please send relevant previous work (preferably in an inspectable format such as Figma or Invision).

```html
<!DOCTYPE html>
<html lang="en">
<head>
<meta charset="utf-8">
<title>Harbor Self Storage – Lakeview</title>
<link rel="stylesheet" href="https://fonts.googleapis.com/css2?family=Poppins:wght@400;500;600;700&family=Rubik:wght@500;700&display=swap">
<style>
:root{
  --navy:#0b3560;
  --blue:#0d4b86;
  --hero-a:#2d6496;
  --hero-b:#1f4f7f;
  --red:#e1222e;
  --ink:#111;
  --text:#333;
  --grey-bg:#f3f3f3;
  --bar:#eeeeee;
  --ghost:#d9dde3;
  --white:#fff;
}
*{box-sizing:border-box;margin:0;padding:0}
html,body{width:1200px;height:3237px;overflow:hidden}
body{position:relative;font-family:'Poppins',sans-serif;color:var(--text);background:var(--white)}
.abs{position:absolute}
h1,h2,h3{font-family:'Rubik',sans-serif;font-weight:700;letter-spacing:1px;color:var(--ink)}
.red{color:var(--red)}

/* header */
.topbar{left:450px;top:0;width:750px;height:63px;background:var(--bar);clip-path:polygon(0 0,100% 0,100% 100%,50px 100%)}
.topbar-item{top:16px;display:flex;align-items:center;gap:14px;font-size:15px;color:#333}
.circle-ic{width:34px;height:34px;border:1.5px solid var(--navy);border-radius:50%;display:flex;align-items:center;justify-content:center}
.brand{left:98px;top:22px;display:flex;align-items:center;gap:10px}
.brand-square{width:26px;height:26px;background:var(--red)}
.brand-name{font-family:'Poppins',sans-serif;font-weight:700;font-size:21px;line-height:1.05;color:var(--navy);letter-spacing:.5px}
.nav{top:86px;left:420px;display:flex;gap:40px;font-size:16px;font-weight:500;color:var(--navy);letter-spacing:.5px}

/* hero */
.hero{left:0;top:123px;width:1200px;height:650px;background:linear-gradient(120deg,var(--hero-a),var(--hero-b));clip-path:polygon(0 0,100% 0,100% 612px,603px 650px,0 591px)}
.hero-photo{left:0;top:160px;width:510px;height:590px;background:linear-gradient(160deg,#8a8f6a,#5d6a48 60%,#2f5a80);border-radius:0 0 40px 0;clip-path:polygon(0 0,100% 0,100% 100%,0 94%)}
.hero-sub{left:522px;top:330px;color:#fff;font-family:'Rubik',sans-serif;font-weight:500;font-size:34px;letter-spacing:1px}
.hero-title{left:522px;top:375px;color:#fff;font-size:52px;letter-spacing:2px}
.hero-text{left:522px;top:453px;width:560px;color:#fff;font-size:15.5px;line-height:30px}

/* skewed buttons */
.btn{display:block;position:absolute;width:168px;height:44px}
.btn .face{position:absolute;inset:0;transform:skewX(-20deg);background:var(--navy)}
.btn .edge{position:absolute;left:-8px;top:3px;width:168px;height:44px;transform:skewX(-20deg);border-left:2px solid var(--navy);border-bottom:2px solid var(--navy)}
.btn span{position:relative;display:block;text-align:center;line-height:44px;color:#fff;font-size:16px;font-weight:500}
.btn.light .face{background:#fff}
.btn.light .edge{border-color:#fff}
.btn.light span{color:var(--ink);font-family:'Rubik',sans-serif;font-weight:700;font-size:20px}

/* about */
.ghost{color:var(--ghost);font-family:'Poppins',sans-serif;font-weight:500;white-space:nowrap}
.about-title{left:0;width:1200px;top:880px;text-align:center;font-size:29px}
.about-sub{left:0;width:1200px;top:924px;display:flex;justify-content:center;align-items:center;gap:18px;font-family:'Rubik',sans-serif;font-weight:500;font-size:27px;color:var(--ink);letter-spacing:1px}
.about-sub i{display:block;width:96px;height:2px;background:var(--navy)}
.about-text{left:175px;width:850px;top:1000px;text-align:center;font-size:15px;line-height:26px;color:#222}
.about-text p+p{margin-top:10px}

/* services */
.services{left:0;top:1330px;width:1200px;height:873px;background:var(--grey-bg)}
.svc-title{font-size:29px;display:flex;align-items:center;gap:10px}
.svc-title i{display:inline-block;width:108px;height:2px;background:var(--red)}
.svc-text{font-size:15px;line-height:25.6px;color:#333}
.photo-frame{border:2px dashed var(--red);border-radius:8px}
.photo{border-radius:8px}

/* faq */
.faq-title{left:0;width:1200px;top:2298px;text-align:center;font-size:30px}
.faq-title-line{left:574px;top:2343px;width:52px;height:3px;background:var(--red)}
.faq-item{left:177px;width:836px;border:1px solid #cfd3d8;background:#f4f4f4;display:flex;align-items:center;justify-content:space-between;padding:0 16px 0 17px;font-size:22px;color:var(--navy)}
.faq-item b{font-weight:600}
.faq-open{left:177px;top:2384px;width:836px;height:126px;background:var(--navy);color:#fff;padding:18px 28px 0 26px}
.faq-open h4{font-weight:400;font-size:22px}
.faq-open h4 b{font-weight:600;font-size:26px}
.faq-open p{font-size:14.5px;line-height:26px;margin:8px 0 0 22px;width:720px}
.toggle{width:32px;height:32px;border-radius:50%;display:flex;align-items:center;justify-content:center;font-size:22px;font-weight:600}
.toggle.dark{background:#111;color:#fff}
.toggle.light{background:#fff;color:var(--navy);position:absolute;right:16px;top:20px}

/* footer */
.footer{left:0;top:2740px;width:1200px;height:497px;background:var(--blue);clip-path:polygon(0 57px,603px 0,100% 57px,100% 100%,0 100%)}
.foot-brand{left:0;width:1200px;top:2830px;display:flex;justify-content:center;align-items:center;gap:12px}
.foot-brand .brand-square{background:#fff}
.foot-brand .brand-name{color:#fff;font-size:34px;text-align:left}
.foot-nav{left:0;width:1200px;top:2976px;display:flex;justify-content:center;gap:40px;color:#fff;font-size:16px;font-weight:500;letter-spacing:.5px}
.contact{top:3047px;display:flex;gap:26px;color:#fff;font-size:15px;font-weight:500;line-height:26px}
.contact .dot{width:58px;height:58px;border-radius:50%;background:var(--red);display:flex;align-items:center;justify-content:center;flex:none}
.vsep{top:3045px;width:1px;height:62px;background:rgba(255,255,255,.5)}
.dash{left:98px;top:3150px;width:1004px;border-top:1.5px dashed rgba(255,255,255,.75)}
.copy{left:96px;top:3182px;color:#fff;font-size:15px}
.pay{top:3181px;height:28px;display:flex;align-items:center;justify-content:center;font-size:10px;font-weight:600}
</style>
</head>
<body>

<!-- header -->
<div class="abs topbar"></div>
<div class="abs topbar-item" style="left:553px">
  <span class="circle-ic"><svg width="14" height="18" viewBox="0 0 14 18"><path d="M7 0C3 0 0 3 0 7c0 5 7 11 7 11s7-6 7-11c0-4-3-7-7-7z" fill="none" stroke="#0b3560" stroke-width="1.6"/><circle cx="7" cy="7" r="2.3" fill="#0b3560"/></svg></span>
  2870 Harbor Street, Lakeview, CA 90000
</div>
<div class="abs topbar-item" style="left:922px">
  <span class="circle-ic"><svg width="16" height="16" viewBox="0 0 24 24"><path d="M6.6 10.8a15 15 0 006.6 6.6l2.2-2.2c.3-.3.7-.4 1-.2 1.1.4 2.3.6 3.6.6.6 0 1 .4 1 1V20c0 .6-.4 1-1 1C10.6 21 3 13.4 3 4c0-.6.4-1 1-1h3.5c.6 0 1 .4 1 1 0 1.3.2 2.5.6 3.6.1.3 0 .7-.2 1z" fill="#0b3560"/></svg></span>
  +1 555-010-0142
</div>
<div class="abs brand">
  <span class="brand-square"></span>
  <span class="brand-name">HARBOR<br>SELF STORAGE</span>
</div>
<nav class="abs nav"><span>HARBOR</span><span>UNIT SIZES</span><span>SPECIALS</span><span>TESTIMONIALS</span><span>PAY FOR</span><span>CONTACT</span></nav>

<!-- hero -->
<div class="abs hero" role="img" aria-label="Rows of storage unit doors along a driveway, tinted blue"></div>
<div class="abs hero-photo" role="img" aria-label="Smiling man in a green jacket carrying a cardboard box"></div>
<div class="abs hero-sub">WELCOME TO</div>
<h1 class="abs hero-title">HARBOR SELF STORAGE</h1>
<p class="abs hero-text">Lorem ipsum dolor sit amet, consectetur adipiscing elit, sed do eiusmod tempor incididunt ut labore et dolore magna aliqua.</p>
<a class="btn light" style="left:533px;top:541px"><i class="edge"></i><i class="face"></i><span>UNITS</span></a>

<!-- about -->
<div class="abs ghost" style="left:1117px;top:1135px;font-size:50px;transform:rotate(-90deg);transform-origin:left top">ABOUT US</div>
<h2 class="abs about-title">WELCOME TO <span class="red">HARBOR SELF STORAGE</span></h2>
<div class="abs about-sub"><i></i>IN LAKEVIEW<i></i></div>
<div class="abs about-text">
  <p>Harbor Self Storage Lakeview Located on Harbor St. between Elm Ave. and Birch Ave. near Lakeview Town Hall in Pine Valley.</p>
  <p>For most people, finding self storage is a matter of locating the intersection of convenience, security, quality, and price. This isn't such a simple equation. On our website you can find our self storage price quickly and easily. We've got a great selection of storage units of various sizes in the heart of Pine Valley - downtown area Lakeview.</p>
</div>
<a class="btn" style="left:514px;top:1207px"><i class="edge"></i><i class="face"></i><span>READ MORE</span></a>

<!-- services -->
<div class="abs services"></div>
<div class="abs ghost" style="left:22px;top:1930px;font-size:50px;transform:rotate(-90deg);transform-origin:left top;color:#dde1e8">OUR SERVICES</div>

<h2 class="abs svc-title" style="left:100px;top:1420px">DRIVE-UP&nbsp;<span class="red">SPACES</span><i></i></h2>
<p class="abs svc-text" style="left:100px;top:1476px;width:455px">Lorem ipsum dolor sit amet, consectetur adipiscing elit, sed do eiusmod tempor incididunt ut labore et dolore magna aliqua. Ut enim ad minim veniam, quis nostrud exercitation ullamco laboris nisi ut aliquip ex ea commodo consequat. Duis aute irure dolor in reprehenderit in voluptate velit esse cillum dolore eu fugiat nulla pariatur</p>
<a class="btn" style="left:95px;top:1667px"><i class="edge"></i><i class="face"></i><span>READ MORE</span></a>
<div class="abs photo-frame" style="left:626px;top:1406px;width:486px;height:314px"></div>
<div class="abs photo" style="left:612px;top:1418px;width:485px;height:314px;background:linear-gradient(135deg,#4f6d8e,#8b8a6e 50%,#c9b28f)" role="img" aria-label="Man and woman holding cardboard boxes in front of storage units"></div>

<div class="abs photo-frame" style="left:83px;top:1798px;width:486px;height:314px"></div>
<div class="abs photo" style="left:97px;top:1810px;width:485px;height:314px;background:linear-gradient(100deg,#9a9a9a,#d8d8d8 35%,#6b6b6b 75%,#2c2c2c)" role="img" aria-label="Indoor corridor lined with white roll-up storage doors"></div>
<h2 class="abs" style="left:661px;top:1810px;font-size:29px;line-height:45px">JUST SHOW UP WITH<br><span class="red">YOUR STUFF</span><span style="display:inline-block;width:108px;height:2px;background:var(--red);vertical-align:middle"></span></h2>
<p class="abs svc-text" style="left:661px;top:1913px;width:455px">Lorem ipsum dolor sit amet, consectetur adipiscing elit, sed do eiusmod tempor incididunt ut labore et dolore magna aliqua. Ut enim ad minim veniam, quis nostrud exercitation ullamco laboris nisi ut aliquip ex ea commodo consequat.</p>
<a class="btn" style="left:656px;top:2058px"><i class="edge"></i><i class="face"></i><span>READ MORE</span></a>

<!-- faq -->
<div class="abs ghost" style="left:1188px;top:2270px;font-family:'Rubik',sans-serif;font-weight:700;font-size:90px;transform:rotate(90deg);transform-origin:left top;color:#eef0f3">FAQ</div>
<h2 class="abs faq-title">FREQUENTLY ASKED <span class="red">QUESTIONS</span></h2>
<div class="abs faq-title-line"></div>
<div class="abs faq-open">
  <h4><b>1.</b>What should I bring to rent a space?</h4>
  <p>Lorem ipsum dolor sit amet, consectetur adipiscing elit, sed do eiusmod tempor incididunt ut labore et dolore magna aliqua. Ut enim ad minim veniam, quis nostrud exercitation.</p>
  <span class="toggle light">-</span>
</div>
<div class="abs faq-item" style="top:2520px;height:69px"><span><b>2.</b> Sed ut perspiciatis unde omnis iste natus</span><span class="toggle dark">+</span></div>
<div class="abs faq-item" style="top:2599px;height:69px"><span><b>3.</b> Sed ut perspiciatis unde omnis iste natus</span><span class="toggle dark">+</span></div>

<!-- footer -->
<div class="abs footer"></div>
<div class="abs foot-brand">
  <span class="brand-square" style="width:36px;height:36px"></span>
  <span class="brand-name">HARBOR<br>SELF STORAGE</span>
</div>
<nav class="abs foot-nav"><span>HARBOR</span><span>UNIT SIZES</span><span>SPECIALS</span><span>TESTIMONIALS</span><span>PAY FOR</span><span>CONTACT</span></nav>

<div class="abs contact" style="left:143px">
  <span class="dot"><svg width="18" height="24" viewBox="0 0 14 18"><path d="M7 0C3 0 0 3 0 7c0 5 7 11 7 11s7-6 7-11c0-4-3-7-7-7z" fill="#fff"/><circle cx="7" cy="7" r="2.4" fill="#e1222e"/></svg></span>
  <span>2870 Harbor Street<br>Lakeview, CA 90000</span>
</div>
<div class="abs vsep" style="left:454px"></div>
<div class="abs contact" style="left:489px">
  <span class="dot"><svg width="24" height="24" viewBox="0 0 24 24"><path d="M6.6 10.8a15 15 0 006.6 6.6l2.2-2.2c.3-.3.7-.4 1-.2 1.1.4 2.3.6 3.6.6.6 0 1 .4 1 1V20c0 .6-.4 1-1 1C10.6 21 3 13.4 3 4c0-.6.4-1 1-1h3.5c.6 0 1 .4 1 1 0 1.3.2 2.5.6 3.6.1.3 0 .7-.2 1z" fill="#fff"/></svg></span>
  <span>Phone<br>+1 555-010-0142</span>
</div>
<div class="abs vsep" style="left:737px"></div>
<div class="abs contact" style="left:771px">
  <span class="dot"><svg width="28" height="22" viewBox="0 0 28 22"><rect x="1.5" y="1.5" width="25" height="19" rx="2" fill="none" stroke="#fff" stroke-width="2.2"/><path d="M2 3l12 9 12-9" fill="none" stroke="#fff" stroke-width="2.2"/></svg></span>
  <span>Opening times<br>9:30 AM - 5:30 PM,<br>7 days a week</span>
</div>
<div class="abs dash"></div>
<div class="abs copy">© copyrights 2022 Harborselfstorage &nbsp;|&nbsp; All Rights Reserved</div>
<div class="abs pay" style="left:605px;width:238px;background:#f7c233;color:#0b3560">Quick Pay</div>
<div class="abs pay" style="left:858px;width:252px;background:#111;color:#fff">Debit or Credit Card</div>
<div class="abs" style="left:1156px;top:3189px;color:#fff;font-size:10px">C25</div>

</body>
</html>
```